Veltrane Group Business Card Design

The CEO is looking for a new trendy look for his business card.
You can stay with current branding or come up with something new/creative. It can be 3D, including Medical Office buildings. You can use our logo in a variety of colors. Please include name, title, company name, company website, email address, cell number

Target Market(s)

Real Estate Development and Construction

Industry/Entity Type

Health care real estate

Contact Information for Business Card

Rohesh Kamdar, CEO M-604.781.2249 E-roheshkamdar@veltrane.com Address:4180 Lindqvist Ave, Tampa, FL 33482 www.veltrane.com

Font styles to use
Other font styles liked:
• Be creative

Requirements
Must have
• Creative, trendy look
Nice to have
• Please go to our website to get a feel- www. veltrane.com
Should not have
• small fonts

```html
<!DOCTYPE html>
<html lang="en">
<head>
<meta charset="utf-8">
<title>Veltrane Group — Business Card</title>
<link href="https://fonts.googleapis.com/css2?family=Poppins:wght@400;500;800&display=swap" rel="stylesheet">
<style>
  :root {
    --bg: #1c1c1c;
    --card: #ffffff;
    --red: #c8121f;
    --red-dark: #9e0e18;
    --navy: #1f2d4d;
    --ink: #2a2a2a;
    --grid-a: #eceeef;
    --grid-b: #ffffff;
  }
  * { box-sizing: border-box; margin: 0; padding: 0; }
  html, body {
    width: 1200px; height: 1015px; overflow: hidden;
    background: var(--bg);
    font-family: "Poppins", sans-serif;
  }
  .stage {
    width: 1200px; height: 1015px;
    display: flex; flex-direction: column; align-items: center; justify-content: center;
    gap: 56px;
  }
  .card {
    position: relative;
    width: 700px; height: 400px;
    background: var(--card);
    overflow: hidden;
    box-shadow: 0 18px 40px rgba(0,0,0,.55);
  }
  .card__texture {
    position: absolute; inset: 0;
    background: linear-gradient(120deg, var(--grid-a) 0%, var(--grid-b) 70%);
  }
  .card__shapes { position: absolute; inset: 0; }
  .wordmark {
    position: absolute;
    font-weight: 800; color: var(--red);
    letter-spacing: -1px; line-height: 1;
    white-space: nowrap;
  }
  .card--front .wordmark { right: 40px; top: 172px; font-size: 42px; }
  .card--back .wordmark { left: 250px; top: 70px; font-size: 42px; }
  .contact {
    position: absolute; left: 270px; top: 160px;
    border-left: 2px solid var(--red);
    padding-left: 16px;
  }
  .contact__name { font-weight: 800; color: var(--red); font-size: 26px; line-height: 1.1; }
  .contact__title { font-weight: 500; color: var(--navy); font-size: 18px; margin-bottom: 12px; }
  .contact__list { list-style: none; }
  .contact__item {
    display: flex; align-items: center; gap: 10px;
    font-size: 17px; color: var(--ink); line-height: 1.55;
  }
  .contact__item svg { width: 16px; height: 16px; flex: none; }
  .contact__address { margin-top: 12px; font-size: 17px; color: var(--ink); line-height: 1.35; }
</style>
</head>
<body>
<main class="stage">

  <section class="card card--front" aria-label="Card front">
    <div class="card__texture" role="img" aria-label="Light grey grid pattern of squares with dots"></div>
    <svg class="card__shapes" viewBox="0 0 700 400" aria-hidden="true">
      <polygon points="0,0 330,0 200,400 0,400" fill="var(--red)"/>
      <polygon points="0,0 300,0 175,400 0,400" fill="var(--card)"/>
      <polygon points="0,0 288,0 164,400 0,400" fill="var(--red)"/>
      <polygon points="0,0 190,0 95,400 0,400" fill="var(--red-dark)" opacity=".55"/>
      <polygon points="0,40 150,40 75,400 0,400" fill="var(--card)"/>
      <polygon points="0,52 138,52 64,400 0,400" fill="var(--red)"/>
      <rect x="440" y="14" width="260" height="7" fill="var(--red)"/>
      <rect x="340" y="42" width="360" height="7" fill="var(--red)"/>
      <rect x="280" y="70" width="100" height="7" rx="3.5" fill="var(--red)"/>
      <rect x="410" y="70" width="50" height="7" rx="3.5" fill="var(--red)"/>
    </svg>
    <div class="wordmark">Veltrane Group</div>
  </section>

  <section class="card card--back" aria-label="Card back">
    <div class="card__texture" role="img" aria-label="Light grey grid pattern of squares with dots"></div>
    <svg class="card__shapes" viewBox="0 0 700 400" aria-hidden="true">
      <polygon points="0,0 200,0 95,400 0,400" fill="var(--red)"/>
      <polygon points="0,0 170,0 72,400 0,400" fill="var(--card)"/>
      <polygon points="0,0 158,0 62,400 0,400" fill="var(--red)"/>
      <rect x="420" y="16" width="280" height="7" fill="var(--red)"/>
      <rect x="250" y="40" width="60" height="7" rx="3.5" fill="var(--red)"/>
    </svg>
    <div class="wordmark">Veltrane Group</div>
    <div class="contact">
      <p class="contact__name">Rohesh Kamdar</p>
      <p class="contact__title">CEO</p>
      <ul class="contact__list">
        <li class="contact__item">
          <svg viewBox="0 0 16 16"><path d="M4 1l3 3-2 2c1 2 3 4 5 5l2-2 3 3-2 3C7 15 1 9 1 3z" fill="var(--red)"/></svg>
          604.781.2249
        </li>
        <li class="contact__item">
          <svg viewBox="0 0 16 16"><rect x="1" y="3" width="14" height="10" fill="var(--red)"/><path d="M1 3l7 6 7-6" fill="none" stroke="#fff" stroke-width="1.4"/></svg>
          roheshkamdar@veltrane.com
        </li>
        <li class="contact__item">
          <svg viewBox="0 0 16 16"><circle cx="8" cy="8" r="7" fill="var(--red)"/><path d="M1 8h14M8 1c-3 4-3 10 0 14M8 1c3 4 3 10 0 14" fill="none" stroke="#fff" stroke-width="1"/></svg>
          www.veltrane.com
        </li>
      </ul>
      <p class="contact__address">4180 Lindqvist Ave, Tampa<br>FL 33482</p>
    </div>
  </section>

</main>
</body>
</html>
```